National Sales - Pick Up Truck Dealer

We need a logo design for a new vehicle dealership based in Sydney, Australia. The business name is Coastal Iron Haulers Motor Co. We will be selling American 'trucks/pick up trucks' like KRV, Torvan, Blaxer, Morrow T420, Kenzo Raptors, Morrow T640 and the likes.

These vehicles are a luxury option and we would like the logo to be strong, luxurious and masculine.Colours will be black and red or black and blue with the option of grey and white.

Target Market(s)

Men

Industry/Entity Type

Car Dealer

Contact Information for Business Card

Dennis Harlowe
Managing Director
0412 639 274
den@qelvtrk.com.au

Level 5, Brindle Parkway
17 Pemberly Lane
Baulkham Hills
NSW
Australia
Licence No: MD493152

Back of the card

qelvtrk.com.au

Font styles to use
Sans Serif

Colors

Designer to choose colors to be used in the design.

Requirements
Must have
• The company logo that is in the attachments, you can choose from the three which one you would like to work with. Must have vehicle images ....Please look at the attachments as they show examples of what we like and also provides potential images. If you choose to put an image on the front even if it is just the front of the vehicle can you please use the Black KRV Sorrento. Must have all details from the business card details section front and back
Nice to have
• N/A
Should not have
• No cars or standard trucks, please refer to the attached images to understand the product . Should not have any new logos or branding. No other colours besides what is in the logo you choose.

```html
<!DOCTYPE html>
<html lang="en">
<head>
<meta charset="utf-8">
<title>Coastal Iron Haulers Motor Co – Business Card</title>
<link rel="stylesheet" href="https://fonts.googleapis.com/css2?family=Open+Sans:wght@400;600;700&family=Orbitron:wght@500&display=swap">
<style>
  :root {
    --backdrop: #3a3a3a;
    --card-dark: #252324;
    --accent-blue: #3aa9e0;
    --blue-light: #3eaee2;
    --blue-deep: #0d5a92;
    --text-light: #e6e6e6;
    --white: #ffffff;
  }
  * { margin: 0; padding: 0; box-sizing: border-box; }
  html, body {
    width: 1200px; height: 900px; overflow: hidden;
    background: var(--backdrop);
    font-family: "Open Sans", Arial, sans-serif;
  }
  .stage { position: relative; width: 1200px; height: 900px; }

  .card { position: absolute; top: 200px; width: 311px; height: 502px; }
  .card-front {
    left: 253px;
    background: var(--card-dark);
    border-radius: 62px 0 62px 0;
  }
  .card-back {
    left: 627px; width: 309px;
    background: radial-gradient(ellipse 75% 60% at 50% 52%, var(--blue-light) 0%, #1f82bf 55%, var(--blue-deep) 100%);
    border-radius: 0 62px 0 62px;
  }

  .brand-name {
    position: absolute; left: 0; right: 0;
    text-align: center;
    font-weight: 700;
    text-transform: uppercase;
    line-height: 1.15;
  }
  .card-front .brand-name { top: 130px; font-size: 24px; color: var(--text-light); }
  .card-back .brand-name { top: 215px; font-size: 24px; color: var(--white); }

  .contact { position: absolute; left: 34px; top: 311px; color: var(--text-light); font-size: 15px; line-height: 18px; }
  .person-name {
    font-family: "Orbitron", "Open Sans", sans-serif;
    font-weight: 500; font-size: 16px; letter-spacing: 2px;
    color: var(--accent-blue); text-transform: uppercase;
  }
  .person-role { margin-top: 1px; }
  .contact-lines { margin-top: 19px; list-style: none; }
  .contact-lines li { display: flex; align-items: center; gap: 2px; }
  .contact-lines svg { width: 12px; height: 12px; fill: var(--accent-blue); }
  .address { margin-top: 8px; font-style: normal; }

  .back-url {
    position: absolute; left: 0; right: 0; top: 438px;
    text-align: center; color: var(--white);
    font-size: 14px; letter-spacing: 1.5px;
  }
</style>
</head>
<body>
<main class="stage">
  <section class="card card-front">
    <div class="brand-name">Coastal Iron<br>Haulers Motor Co</div>
    <div class="contact">
      <p class="person-name">Dennis Harlowe</p>
      <p class="person-role">Managing Director</p>
      <ul class="contact-lines">
        <li>
          <svg viewBox="0 0 12 12" aria-hidden="true"><path d="M1 4 Q6 0 11 4 L9.5 5.5 L8 4.5 L8 3.5 Q6 3 4 3.5 L4 4.5 L2.5 5.5 Z M3 6 H9 L10 10.5 H2 Z"/></svg>
          0412 639 274
        </li>
        <li>
          <svg viewBox="0 0 12 12" aria-hidden="true"><circle cx="6" cy="6" r="5.5"/></svg>
          qelvtrk.com.au
        </li>
      </ul>
      <address class="address">
        Level 5, Brindle Parkway<br>
        17 Pemberly Lane<br>
        Fernley Hills WDR, Australia
      </address>
    </div>
  </section>

  <section class="card card-back">
    <div class="brand-name">Coastal Iron<br>Haulers Motor Co</div>
    <p class="back-url">qelvtrk.com.au</p>
  </section>
</main>
</body>
</html>
```